Redesign of Form/Document Navigation Page

I need a redesign of our document and navigation bar on the left. We want the same navigation bar layout/setup but want the buttons and typography to be simple and matching all over. The form needs to be aesthetically pleasing and fit within the page.

1st attachment is our Direct Deposit and the second is the form continued.

```html
<!DOCTYPE html>
<html lang="en">
<head>
<meta charset="utf-8">
<title>Direct Deposit – Sentinel Watch Services</title>
<link href="https://fonts.googleapis.com/css2?family=Open+Sans:wght@400;600;700&display=swap" rel="stylesheet">
<style>
  :root{
    --navy:#262262;
    --gold:#ecb020;
    --gold-dark:#e39a12;
    --btn-text:#5a3a00;
    --band:#ebebeb;
    --panel:#f4f4f4;
    --field-border:#c9c9c9;
    --ink:#222;
    --link:#5a5196;
    --heading:#2e2a6e;
    --track:#dcdcdc;
  }
  *{box-sizing:border-box;margin:0;padding:0}
  html,body{width:1200px;height:826px;overflow:hidden;background:#fff;font-family:"Open Sans",Arial,sans-serif;color:var(--ink)}
  .page{position:relative;width:1200px;height:826px}

  .site-header{position:absolute;left:0;top:0;width:1200px;height:110px}
  .brand{position:absolute;left:132px;top:28px;display:flex;align-items:center;gap:10px}
  .brand-dot{width:50px;height:50px;border-radius:50%;background:var(--navy)}
  .brand-name{color:var(--gold);font-weight:700;font-size:24px;line-height:25px;text-transform:uppercase;letter-spacing:.3px}
  .top-nav{position:absolute;left:828px;top:47px;display:flex;align-items:center;font-size:12px}
  .top-nav a{color:var(--link);text-decoration:none;display:flex;align-items:center;gap:3px;margin-right:18px}
  .top-nav svg{width:11px;height:11px;fill:var(--link)}
  .user{position:absolute;left:962px;top:37px;display:flex;align-items:center;gap:7px;font-size:12px;color:#111}
  .avatar{width:36px;height:36px;border-radius:50%;background:linear-gradient(135deg,#d9b79a,#8a6a55)}

  .sub-band{position:absolute;left:0;top:110px;width:1200px;height:40px;background:var(--band)}
  .back-btn{position:absolute;left:132px;top:0;width:112px;height:40px;background:var(--navy);color:#fff;font-size:12px;display:flex;align-items:center;justify-content:center;gap:5px}
  .back-btn svg{width:9px;height:9px}

  .side-nav{position:absolute;left:132px;top:170px;width:240px}
  .nav-item{position:relative;height:80px;margin-bottom:2.5px;background:var(--navy);color:#fff;display:flex;align-items:center;font-size:15px}
  .nav-item svg{width:28px;height:24px;margin-left:22px;margin-right:12px;fill:none;stroke:#fff;stroke-width:2}
  .nav-item.active{background:var(--gold)}
  .nav-item.active::after{content:"";position:absolute;right:-14px;top:30px;border-left:14px solid var(--gold);border-top:10px solid transparent;border-bottom:10px solid transparent}

  .doc-panel{position:absolute;left:376px;top:170px;width:691px;height:574px;background:var(--panel)}
  .scroll-track{position:absolute;left:678px;top:8px;width:5px;height:560px;background:var(--track)}
  .scroll-thumb{position:absolute;left:0;bottom:0;width:5px;height:80px;background:var(--navy)}
  .accept-btn{position:absolute;left:30px;top:32px;width:160px;height:48px;border-radius:2px;background:linear-gradient(#f0b520,var(--gold-dark));color:var(--btn-text);font-size:14.4px;font-weight:600;display:flex;align-items:center;justify-content:center}
  .sign-heading{position:absolute;left:31px;top:126px;font-size:14.4px;font-weight:400;color:var(--heading);line-height:20px}
  .field-label{position:absolute;font-size:14.4px;line-height:20px;color:#111}
  .field-box{position:absolute;height:48px;background:#fff;border:1px solid var(--field-border)}
  .l-company{left:30px;top:166px}
  .b-company{left:31px;top:189px;width:192px}
  .l-comments{left:248px;top:166px}
  .b-comments{left:249px;top:189px;width:410px}
  .l-file{left:30px;top:262px}
  .b-file{left:31px;top:285px;width:192px}

  .site-footer{position:absolute;left:0;top:770px;width:1200px;height:56px;background:var(--band);font-size:12px;color:#333;text-align:center;line-height:56px}
</style>
</head>
<body>
<div class="page">
  <header class="site-header">
    <div class="brand"><span class="brand-dot"></span><span class="brand-name">Sentinel Watch<br>Services</span></div>
    <nav class="top-nav">
      <a href="#"><svg viewBox="0 0 12 12"><path d="M6 1L0 6h2v5h3V8h2v3h3V6h2z"/></svg>Home</a>
      <a href="#"><svg viewBox="0 0 12 12"><circle cx="6" cy="6" r="5" fill="none" stroke="#5a5196" stroke-width="2"/><circle cx="6" cy="6" r="2"/></svg>Help</a>
    </nav>
    <div class="user"><div class="avatar" role="img" aria-label="User profile photo"></div>Dana Reyes</div>
  </header>

  <div class="sub-band">
    <div class="back-btn"><svg viewBox="0 0 10 10" fill="none" stroke="#fff" stroke-width="1.6"><path d="M5 1L1 5l4 4M9 1L5 5l4 4"/></svg>Back To Profile</div>
  </div>

  <nav class="side-nav">
    <div class="nav-item active"><svg viewBox="0 0 28 24"><rect x="1" y="5" width="26" height="15" rx="1"/><circle cx="14" cy="12.5" r="4"/></svg>Direct Deposit</div>
    <div class="nav-item"><svg viewBox="0 0 28 24"><path d="M8 1h9l5 5v17H8z"/><path d="M11 11h8M11 15h8M11 19h8"/></svg>Change W-4</div>
    <div class="nav-item"><svg viewBox="0 0 28 24"><path d="M4 12h12M11 7l5 5-5 5"/><path d="M17 3h6v18h-6"/></svg>Labour Code</div>
    <div class="nav-item"><svg viewBox="0 0 28 24"><circle cx="14" cy="12" r="11" fill="#fff"/><path d="M14 6v8M14 16v2" stroke="#262262" stroke-width="3"/></svg>Personal Information</div>
    <div class="nav-item"><svg viewBox="0 0 28 24"><rect x="2" y="6" width="24" height="16" rx="2"/><path d="M10 6V2h8v4M14 10v8M10 14h8"/></svg>Appraisal and Review</div>
    <div class="nav-item"><svg viewBox="0 0 28 24"><path d="M4 4h8v12H4zM13 9h10v14H13z"/></svg>Write Up-Slip</div>
    <div class="nav-item"><svg viewBox="0 0 28 24"><path d="M2 2v20h24M7 18v-6M11 18V10M15 18v-8M19 18V6"/></svg>Employee Performance</div>
  </nav>

  <main class="doc-panel">
    <div class="accept-btn">Accept Document</div>
    <h2 class="sign-heading">Only Payroll Manager Signs Below</h2>
    <label class="field-label l-company">Company Name :</label>
    <div class="field-box b-company"></div>
    <label class="field-label l-comments">Comments</label>
    <div class="field-box b-comments"></div>
    <label class="field-label l-file">Employee File Number :</label>
    <div class="field-box b-file"></div>
    <div class="scroll-track"><div class="scroll-thumb"></div></div>
  </main>

  <footer class="site-footer">Copyright &nbsp;©&nbsp; 2016 &nbsp;Company name. &nbsp;All rights reserved.</footer>
</div>
</body>
</html>
```